Business card design and logo needed - Photographer

I take photos of weddings, rodeos, snowmobiling.
Need a card to hand out to prospective clients.
Industry/Entity Type
Business
Contact Information for Business Card
Marcus Tollen Photography
Requirements
Must have
- Bold
Black or white base.
My website. www.MarcusTollen-example.com
Should not have
- camera/ lens/ aperture blades

```html
<!DOCTYPE html>
<html lang="en">
<head>
<meta charset="utf-8">
<title>Marcus Tollen Photography – Business Card</title>
<link rel="stylesheet" href="https://fonts.googleapis.com/css2?family=Pinyon+Script&family=Inconsolata:wght@500&display=swap">
<style>
  :root {
    --page: #ffffff;
    --card-deep: #15161c;
    --card-mid: #2c2d35;
    --ink-light: #ececee;
    --chip-face: #dcdcde;
    --chip-edge: #b9b9bd;
    --chip-ink: #1d1d22;
    --photo-frame: #ffffff;
  }
  * { margin: 0; padding: 0; box-sizing: border-box; }
  html, body {
    width: 900px; height: 1200px; overflow: hidden;
    background: var(--page);
  }
  .canvas { position: relative; width: 900px; height: 1200px; }

  .card {
    position: absolute;
    overflow: hidden;
    background:
      radial-gradient(ellipse at 50% 45%, var(--card-mid) 0%, var(--card-deep) 85%);
  }
  .card--front { left: 64px; top: 139px; width: 754px; height: 434px; }
  .card--back  { left: 62px; top: 594px; width: 760px; height: 438px; }

  .wordmark {
    position: absolute;
    font-family: "Pinyon Script", cursive;
    font-weight: 400;
    color: var(--ink-light);
    text-align: center;
    line-height: 1;
  }
  .wordmark__name { display: block; }
  .wordmark__trade { display: block; }

  .card--front .wordmark { left: 50px; top: 88px; width: 290px; }
  .card--front .wordmark__name { font-size: 54px; }
  .card--front .wordmark__trade { font-size: 30px; margin-top: 8px; }

  .card--back .wordmark { left: 0; top: 130px; width: 760px; }
  .card--back .wordmark__name { font-size: 76px; }
  .card--back .wordmark__trade { font-size: 40px; margin-top: 10px; }

  .contact-chip {
    position: absolute;
    left: 57px;
    display: flex; align-items: center; justify-content: center;
    background: linear-gradient(#e6e6e8, var(--chip-face));
    border: 2px solid var(--chip-edge);
    box-shadow: 0 2px 4px rgba(0,0,0,0.6);
    font-family: "Inconsolata", monospace;
    font-weight: 500;
    color: var(--chip-ink);
  }
  .contact-chip--phone { top: 235px; width: 324px; height: 42px; font-size: 24px; letter-spacing: 1px; }
  .contact-chip--web   { top: 297px; width: 340px; height: 55px; font-size: 20px; }

  .snapshot {
    position: absolute;
    border: 3px solid var(--photo-frame);
    box-shadow: 0 3px 8px rgba(0,0,0,0.7);
  }
  .snapshot--couple {
    left: 434px; top: 46px; width: 130px; height: 175px;
    transform: rotate(-5deg);
    background: linear-gradient(160deg, #9bb6a8 0%, #5c6b58 45%, #e8e6e2 75%, #6f7f55 100%);
  }
  .snapshot--meadow {
    left: 565px; top: 54px; width: 118px; height: 158px;
    transform: rotate(4deg);
    background: linear-gradient(180deg, #3f6b36 0%, #6fa14c 40%, #a58ab0 80%, #6d5a86 100%);
  }
  .snapshot--walk {
    left: 420px; top: 242px; width: 150px; height: 100px;
    transform: rotate(-24deg);
    background: linear-gradient(120deg, #2b2b2b 0%, #3c3c3c 35%, #5e8a3e 55%, #e9e9e9 85%);
  }
  .snapshot--portrait {
    left: 570px; top: 205px; width: 132px; height: 118px;
    transform: rotate(14deg);
    background: linear-gradient(140deg, #3d5a38 0%, #5c7446 40%, #e2c6a4 70%, #d8b88e 100%);
  }
</style>
</head>
<body>
<main class="canvas">
  <section class="card card--front" aria-label="Business card front">
    <div class="wordmark">
      <span class="wordmark__name">Marcus Tollen</span>
      <span class="wordmark__trade">Photography</span>
    </div>
    <div class="contact-chip contact-chip--phone">(306) 555 0142</div>
    <div class="contact-chip contact-chip--web">www.MarcusTollen-example.com</div>

    <div class="snapshot snapshot--couple" role="img" aria-label="Wedding photo of a bride with a bouquet and groom outdoors"></div>
    <div class="snapshot snapshot--meadow" role="img" aria-label="Photo of a woman in a purple dress sitting on a lawn"></div>
    <div class="snapshot snapshot--walk" role="img" aria-label="Photo of a wedding couple walking on grass"></div>
    <div class="snapshot snapshot--portrait" role="img" aria-label="Close portrait of a blonde woman outdoors"></div>
  </section>

  <section class="card card--back" aria-label="Business card back">
    <div class="wordmark">
      <span class="wordmark__name">Marcus Tollen</span>
      <span class="wordmark__trade">Photography</span>
    </div>
  </section>
</main>
</body>
</html>
```